KRT,LLC

I need a flyer that has my company Logo on it as well as my book cover on it. I need for the flyer to read: "Rust on the harbor gate" ~ A story of Money,Murder,Sex and family ties in the heart of the city. Read along as Desmond L. Ferris masterfully paint this Wilmington,Delaware tale like no other~The "K.T.Z crew" clash in a rain of bullets against North sides own "Pinto crew."
At $14.99 you can own your own copy of "Rust on the harbor gate."
Contact Des Ferris @ 302-555-0147 to purchase your paper back copy.
OR
Visit:www.krtllcbooks-example.com
www.rustontheharborgate-example.com
rustharborgate24@example.net
To purchase your order directly off line.
We accept paxo,TellarPay and debit cards for those individuals who wish to order on-line!

```html
<!DOCTYPE html>
<html lang="en">
<head>
<meta charset="utf-8">
<title>Rust on the harbor gate – Flyer</title>
<link rel="stylesheet" href="https://fonts.googleapis.com/css2?family=Creepster&family=Rye&family=Open+Sans:wght@400;700&display=swap">
<style>
:root{
  --backdrop:#7d1418;
  --paper:#ffffff;
  --ink:#1a1a1a;
  --blood:#a3171c;
  --blood-deep:#6e0f12;
  --alert:#e32222;
  --steel:#3a58a8;
  --gold:#ffc61a;
  --night:#0d0d0d;
  --strip:#8a1418;
}
*{box-sizing:border-box;margin:0;padding:0}
html,body{width:1200px;height:1000px;overflow:hidden;background:var(--backdrop)}
.flyer{position:absolute;left:220px;top:20px;width:760px;height:960px;background:var(--paper);overflow:hidden;font-family:"Open Sans",Arial,sans-serif;color:var(--ink);text-align:center}
.title-main{position:absolute;top:10px;left:0;right:0;font-family:"Creepster",cursive;font-size:150px;line-height:1;color:var(--blood);letter-spacing:4px;font-weight:400}
.title-sub{position:absolute;top:166px;left:0;right:0;font-family:"Rye",serif;font-size:38px;line-height:1.2;color:var(--blood-deep);font-weight:400}
.title-sub .cool{color:var(--steel)}
.tagline{position:absolute;top:220px;left:20px;right:20px;font-size:21px;line-height:1.3}
.tagline strong{color:var(--alert)}
.synopsis{position:absolute;top:252px;left:50px;right:50px;font-size:15.5px;line-height:1.3}
.rival{position:absolute;top:298px;left:0;right:0;font-size:22px;line-height:1.3}
.collage{position:absolute;top:334px;left:0;width:760px;height:320px}
.photo-left{position:absolute;left:0;top:0;width:240px;height:320px;background:linear-gradient(90deg,#7a5a52,#c9a9a3 70%,rgba(255,255,255,0))}
.photo-right{position:absolute;right:0;top:0;width:300px;height:320px;background:linear-gradient(270deg,#6d6c66,#b9bcb3 70%,rgba(255,255,255,0))}
.photo-group{position:absolute;left:230px;top:214px;width:220px;height:106px;background:linear-gradient(180deg,#b7bcc4,#5d6068)}
.photo-street{position:absolute;left:320px;top:0;width:230px;height:92px;background:linear-gradient(180deg,#c9d3de,#8f8a86)}
.book-cover{position:absolute;left:150px;top:48px;width:420px;height:186px;background:linear-gradient(90deg,#2a3a9a 0 48%,#1d2a7a 48% 52%,#2a3a9a 52%);box-shadow:4px 6px 10px rgba(0,0,0,.45);transform:rotate(-2deg)}
.burst{position:absolute;left:470px;top:-8px;width:126px;height:126px}
.price-line{position:absolute;top:660px;left:0;right:0;font-size:19px;line-height:1.3}
.price-line b{font-size:23px}
.price-title{position:absolute;top:686px;left:0;right:0;font-size:27px;line-height:1.3;font-weight:700;color:var(--alert)}
.contact-band{position:absolute;top:730px;left:110px;width:540px;height:50px;background:var(--blood-deep);border-radius:26px 8px 26px 8px;color:var(--gold);font-size:28px;line-height:50px}
.contact-band b{font-weight:700}
.purchase-note{position:absolute;top:788px;left:0;right:0;font-size:15px;line-height:20px}
.or{position:absolute;top:808px;left:0;right:0;font-size:14px;line-height:20px}
.base{position:absolute;left:0;bottom:0;width:760px;height:124px}
.sites{position:absolute;top:872px;left:130px;right:20px;font-size:12.5px;line-height:17px;color:var(--paper)}
.sites .row{display:flex;justify-content:space-around;color:var(--gold);font-weight:700}
.sites .row span:first-child::before{content:"Visit: "}
.sites .mail{color:var(--gold);font-weight:700}
.payment{position:absolute;bottom:0;left:0;width:760px;height:30px;background:var(--strip);color:var(--paper);font-size:13.5px;line-height:30px}
.brand{position:absolute;left:22px;top:882px;display:flex;align-items:center;gap:6px;color:var(--paper);font-size:15px;font-weight:700}
.brand .dot{width:16px;height:16px;border-radius:50%;border:2px solid var(--paper)}
</style>
</head>
<body>
<main class="flyer">
  <h1 class="title-main">RUST</h1>
  <h2 class="title-sub">ON THE HARBOR <span class="cool">GATE</span></h2>
  <p class="tagline">A story of <strong>Money, Murder, Sex and family</strong> ties in the heart of the city.</p>
  <p class="synopsis">Read along as Desmond L. Ferris masterfully paint this Wilmington, Delaware tale like no other~The "K.T.Z crew" clash in a rain of bullets against North sides own</p>
  <p class="rival">"Pinto crew."</p>

  <section class="collage">
    <div class="photo-left" role="img" aria-label="Faded photographs of the story's characters"></div>
    <div class="photo-right" role="img" aria-label="Faded photographs of cash stacks, a street sign and a character"></div>
    <div class="photo-street" role="img" aria-label="Photograph of a man standing by brick houses"></div>
    <div class="photo-group" role="img" aria-label="Photograph of a group of young men on a street"></div>
    <div class="book-cover" role="img" aria-label="Book cover of Rust on the harbor gate, back, spine and front"></div>
    <svg class="burst" viewBox="0 0 100 100">
      <polygon fill="#ffc61a" stroke="#e08a00" stroke-width="1.5" points="50,2 58,18 75,8 75,27 94,26 84,42 98,54 81,62 88,80 69,79 64,97 50,86 36,97 31,79 12,80 19,62 2,54 16,42 6,26 25,27 25,8 42,18"/>
      <text x="50" y="40" text-anchor="middle" font-family="Open Sans, sans-serif" font-weight="700" font-size="15" fill="#a3171c">Buy</text>
      <text x="50" y="60" text-anchor="middle" font-family="Open Sans, sans-serif" font-weight="700" font-size="17" fill="#e32222">$14.99</text>
      <text x="50" y="76" text-anchor="middle" font-family="Open Sans, sans-serif" font-weight="700" font-size="12" fill="#a3171c">Only</text>
    </svg>
  </section>

  <p class="price-line">At <b>$14.99</b> you can own your own copy of</p>
  <p class="price-title">"Rust on the harbor gate."</p>
  <p class="contact-band">Contact Des Ferris @ <b>302-555-0147</b></p>
  <p class="purchase-note">to purchase your paper back copy.</p>
  <p class="or">OR</p>

  <svg class="base" viewBox="0 0 760 124" preserveAspectRatio="none" aria-hidden="true">
    <path d="M0,8 Q380,40 760,8 L760,124 L0,124 Z" fill="#0d0d0d"/>
  </svg>
  <div class="brand"><span class="dot"></span>KRT,LLC</div>
  <div class="sites">
    <div class="row"><span>www.krtllcbooks-example.com</span><span>www.rustontheharborgate-example.com</span></div>
    <div class="mail">rustharborgate24@example.net</div>
    <div>To purchase your order directly off line.</div>
  </div>
  <p class="payment">We accept paxo, TellarPay and debit cards for those individuals who wish to order on-line!</p>
</main>
</body>
</html>
```